"Harbor Builders" is a residential building company and needs a new business card design and may re

We would like a redesign based on the existing logo, and would like to see a new font as well. We are bespoke home builders who build sustainable energy efficient homes.

Industry/Entity Type

Construction

Contact Information for Business Card

Business card size 40mm x 90mm

Colors

Designer to choose colors to be used in the design.

```html
<!DOCTYPE html>
<html lang="en">
<head>
<meta charset="utf-8">
<title>Harbor Builders – Business Card</title>
<link rel="stylesheet" href="https://fonts.googleapis.com/css2?family=Roboto:wght@400;500;700&family=Roboto+Condensed:wght@700&display=swap">
<style>
  :root {
    --backdrop: #5b4737;
    --paper: #f1f1f1;
    --ink: #0b0b0b;
    --text-grey: #4a4a4a;
    --lime: #b2c92c;
    --card-black: #070809;
    --white: #ffffff;
  }
  * { box-sizing: border-box; margin: 0; padding: 0; }
  html, body {
    width: 1200px; height: 960px; overflow: hidden;
    background: var(--backdrop);
    font-family: "Roboto", Arial, sans-serif;
  }
  .canvas { position: relative; width: 1200px; height: 960px; }

  .card { position: absolute; width: 600px; height: 342px; }

  /* Front */
  .card-front { left: 314px; top: 113px; background: var(--paper); color: var(--text-grey); text-align: center; }
  .brand {
    position: absolute; left: 0; right: 0; top: 62px;
    display: flex; justify-content: center; align-items: center; gap: 14px;
  }
  .brand-square { width: 30px; height: 30px; background: var(--lime); }
  .brand-name { font-family: "Roboto", Arial, sans-serif; font-weight: 500; font-size: 36px; color: var(--ink); letter-spacing: 0.5px; }
  .holder-name {
    position: absolute; left: 0; right: 0; top: 160px;
    font-family: "Roboto Condensed", "Arial Narrow", sans-serif;
    font-weight: 700; font-size: 22px; color: var(--ink);
  }
  .company-details { position: absolute; left: 0; right: 0; top: 200px; font-size: 14.5px; line-height: 17.5px; }
  .company-details .company { font-weight: 700; }
  .contact-lines { position: absolute; left: 0; right: 0; top: 263px; font-size: 14.5px; line-height: 19px; }
  .contact-item { display: inline-flex; align-items: center; gap: 4px; }
  .contact-item svg { fill: var(--ink); }
  .edge-band { position: absolute; bottom: 0; height: 10px; }
  .edge-band.black { left: 0; width: 298px; background: var(--ink); }
  .edge-band.lime { left: 301px; right: 0; background: var(--lime); }

  /* Back */
  .card-back { left: 311px; top: 472px; background: var(--card-black); }
  .back-brand {
    position: absolute; left: 0; right: 0; top: 118px;
    display: flex; justify-content: center; align-items: center; gap: 20px;
  }
  .back-brand .brand-square { width: 54px; height: 54px; }
  .back-brand .brand-name { color: var(--white); font-size: 58px; }
  .back-url {
    position: absolute; left: 0; right: 0; top: 297px; text-align: center;
    color: var(--white); font-size: 14px; letter-spacing: 3px;
  }
</style>
</head>
<body>
<main class="canvas">
  <section class="card card-front" aria-label="Business card front">
    <div class="brand">
      <span class="brand-square"></span>
      <span class="brand-name">harbor builders</span>
    </div>
    <h1 class="holder-name">DANIEL FERRARO</h1>
    <div class="company-details">
      <p class="company">Harbor Builders Pty Ltd</p>
      <p>PO Box 4120 Eastgate, LPO Ridgeford WA 6099</p>
      <p>Registration 40587 | ABN: 52 304 918 276</p>
    </div>
    <div class="contact-lines">
      <p>
        <span class="contact-item">
          <svg width="10" height="15" viewBox="0 0 10 15" aria-hidden="true"><path d="M1.5 0h7A1.5 1.5 0 0 1 10 1.5v12A1.5 1.5 0 0 1 8.5 15h-7A1.5 1.5 0 0 1 0 13.5v-12A1.5 1.5 0 0 1 1.5 0zM1.5 2v10h7V2zM5 12.6a.8.8 0 1 0 0 1.6.8.8 0 0 0 0-1.6z"/></svg>
          0400 555 018
        </span>
        <span class="contact-item">
          <svg width="14" height="10" viewBox="0 0 14 10" aria-hidden="true"><path d="M0 0h14v1.2L7 5.6 0 1.2zM0 2.6l7 4.4 7-4.4V10H0z"/></svg>
          daniel@harborbuilders.com.au
        </span>
      </p>
      <p>
        <span class="contact-item">
          <svg width="13" height="13" viewBox="0 0 13 13" aria-hidden="true"><circle cx="6.5" cy="6.5" r="6.5"/><path d="M3 3.5c1.5-.5 2.5.5 2 1.5s-1.5 1-1 2.5S3 9 2.5 8M8 2c1 1 2.5.5 2.5 2S9 5.5 9.5 7.5s-1 3-2 3.5" stroke="#f1f1f1" stroke-width="1.2" fill="none"/></svg>
          www.harborbuilders.com.au
        </span>
      </p>
    </div>
    <span class="edge-band black"></span>
    <span class="edge-band lime"></span>
  </section>

  <section class="card card-back" aria-label="Business card back">
    <div class="back-brand">
      <span class="brand-square"></span>
      <span class="brand-name">harbor builders</span>
    </div>
    <p class="back-url">www.harborbuilders.com.au</p>
  </section>
</main>
</body>
</html>
```